Window Cleaning Leaflet

Hi everyone,

I need a leaflet (couldn't find 'leaflet' as an option when begining this project - so one sided only) to send out to coastal properties in South side Melbourne. The Flyer is aimed at high net individuals, mummies, business people etc who own these properties who don't have time to clean the windows themselves (often multiple levels) and want their home looking fabulous in time for Christmas and NY's celebrations.

I would really love a new and original design for a window washing leaflet. something outside of the norm that 'pops' and makes people feel happy when they look at it.

I guess a point of differentiation is that I'm a female working in a mans industry so appeal to mothers looking for someone who is 'reliable, trustworthy and understanding of peoples needs'.

I have made an outline of what I would like included in the leaflet, so if you could please take a look, feel free to change things around, wording and layout etc. If you can make it sound more professional please do so.

I would like the colours to be 'happy' colours, maybe with a silly season theme?

Overall aesthetically pleasing is a must, I find most window cleaning leaflets fairly mundane and boring, please feel free to think outside the box. The more original the better.

Target Market(s)

People who own large Melbourne homes in affluent suburbs, mainly suburbs with a lot of large coastal properties. Generally owned by high net worth individuals who just don't have tme to clean the windows themselves due to their profession or hectic lifestyles but can afford to pay someone else to do it.

Industry/Entity Type

Window Cleaning

Requirements
Must have
• 1) The name of the business - Kelda’s Window Washing Services
• 2) The coupon special and all details attached:
• Small Homes (up to 12 windows) $120
• Medium Homes (up to 16 windows) $180
• Large Homes (up to 20 windows, 2 storeys) $240
• 20% discount
• *Discount applicable to first time customers only.
• *All services include fly screen, sill and tracks cleaned as well as cobweb removal.
• *Houses with more than 20 windows (or two levels) will have an immediate quote provided upon inspection of the property with 20% discount applied.
• *Kelda’s Window Washing Services are fully insured.
• 3) My contact number - 0418 265 903

```html
<!DOCTYPE html>
<html lang="en">
<head>
<meta charset="utf-8">
<title>Kelda’s Window Washing Services – Leaflet</title>
<link href="https://fonts.googleapis.com/css2?family=Exo+2:wght@500;600&family=Roboto+Condensed:wght@700&family=Arimo:ital,wght@0,400;1,700&display=swap" rel="stylesheet">
<style>
  :root {
    --backdrop: #e9ebee;
    --paper: #ffffff;
    --cyan: #17b2d9;
    --blue: #0a7dc6;
    --pink: #ec4f9d;
    --ink: #2a2a2a;
    --rule: #c9c9c9;
    --photo-top: #d9dcde;
    --photo-mid: #eceeef;
  }
  * { box-sizing: border-box; margin: 0; padding: 0; }
  html, body { width: 864px; height: 1200px; overflow: hidden; background: var(--backdrop); }
  .leaflet {
    position: absolute; left: 13px; top: 5px;
    width: 710px; height: 1008px;
    background: var(--paper);
    transform: scale(1.18); transform-origin: top left;
    font-family: "Arimo", Arial, sans-serif; color: var(--ink);
    overflow: hidden;
  }
  .hero-photo {
    position: absolute; left: 0; top: 0; width: 710px; height: 500px;
    background: linear-gradient(180deg, var(--photo-top) 0%, var(--photo-mid) 60%, var(--paper) 100%);
  }
  .discount-badge {
    position: absolute; left: 40px; top: 276px; width: 176px; height: 176px;
    border-radius: 50%; background: var(--paper);
    box-shadow: 0 2px 6px rgba(0,0,0,.25);
  }
  .discount-badge__inner {
    position: absolute; inset: 8px; border-radius: 50%; background: var(--cyan);
    color: #fff; font-family: "Roboto Condensed", Arial, sans-serif; font-weight: 700;
    display: flex; flex-direction: column; align-items: center; justify-content: center;
    transform: rotate(-14deg);
  }
  .discount-badge__value { font-size: 62px; line-height: .95; }
  .discount-badge__label { font-size: 28px; line-height: 1; }
  .business-name {
    position: absolute; left: 45px; top: 482px;
    font-family: "Exo 2", Arial, sans-serif; font-weight: 500;
    font-size: 52px; line-height: 57px; color: var(--blue);
  }
  .pitch {
    position: absolute; left: 43px; top: 624px; width: 470px;
    font-style: italic; font-weight: 700; font-size: 19px; line-height: 26px; color: var(--cyan);
  }
  .pitch p + p { margin-top: 9px; }
  .intro {
    position: absolute; left: 43px; top: 723px; width: 450px;
    font-size: 20px; line-height: 26px; color: var(--ink);
  }
  .price-card {
    position: absolute; left: 553px; width: 120px; height: 110px;
    border: 2px solid var(--rule); border-radius: 9px; background: var(--paper);
    overflow: hidden; text-align: center;
    font-family: "Roboto Condensed", Arial, sans-serif; font-weight: 700;
  }
  .price-card__head { height: 78px; color: #fff; padding-top: 9px; }
  .price-card__size { font-size: 13.5px; line-height: 16px; }
  .price-card__price { font-size: 44px; line-height: 48px; }
  .price-card__note { font-size: 12px; line-height: 12px; color: var(--ink); padding-top: 8px; }
  .price-card--small { top: 441px; } .price-card--small .price-card__head { background: var(--cyan); }
  .price-card--medium { top: 564px; } .price-card--medium .price-card__head { background: var(--blue); }
  .price-card--large { top: 689px; } .price-card--large .price-card__head { background: var(--pink); }
  .price-card--large .price-card__note { padding-top: 3px; }
  .contact-band {
    position: absolute; left: 0; top: 817px; width: 710px; height: 62px; display: flex;
    font-family: "Roboto Condensed", Arial, sans-serif; font-weight: 700; color: #fff;
  }
  .contact-band__offer {
    width: 350px; background: var(--cyan); font-size: 18px; line-height: 22px;
    padding: 9px 0 0 37px;
  }
  .contact-band__phone {
    flex: 1; background: var(--blue); font-size: 39px; line-height: 62px; padding-left: 16px;
  }
  .terms {
    position: absolute; left: 36px; top: 893px; width: 620px;
    list-style: none; font-size: 13px; line-height: 16px; color: var(--ink);
  }
  .terms li { padding-left: 14px; text-indent: -14px; margin-bottom: 5px; }
  .terms li::before { content: "*"; display: inline-block; width: 14px; text-indent: 0; }
</style>
</head>
<body>
  <main class="leaflet">
    <div class="hero-photo" role="img" aria-label="Bright living room with a landscape painting and fireplace, and a hand holding a window squeegee"></div>

    <div class="discount-badge">
      <div class="discount-badge__inner">
        <span class="discount-badge__value">20%</span>
        <span class="discount-badge__label">Discount</span>
      </div>
    </div>

    <h1 class="business-name">Kelda’s Window<br>Washing Services</h1>

    <div class="pitch">
      <p>Do you need your windows cleaned?</p>
      <p>Are you simply too busy as a hard working parent to do it yourself?</p>
    </div>

    <p class="intro">Kelda’s Window Washing Services provide a reliable, professional service, ensuring that your home will sparkle.</p>

    <div class="price-card price-card--small">
      <div class="price-card__head"><div class="price-card__size">SMALL HOMES</div><div class="price-card__price">$120</div></div>
      <div class="price-card__note">up to 12 windows</div>
    </div>
    <div class="price-card price-card--medium">
      <div class="price-card__head"><div class="price-card__size">MEDIUM HOMES</div><div class="price-card__price">$180</div></div>
      <div class="price-card__note">up to 12 windows</div>
    </div>
    <div class="price-card price-card--large">
      <div class="price-card__head"><div class="price-card__size">LARGE HOMES</div><div class="price-card__price">$240</div></div>
      <div class="price-card__note">up to 20 windows<br>&amp; 2 storeys</div>
    </div>

    <div class="contact-band">
      <div class="contact-band__offer">Call Kelda today and take advantage<br>of our special introductory offer.</div>
      <div class="contact-band__phone">Kelda : 0418 265 903</div>
    </div>

    <ul class="terms">
      <li>Discount applicable to first time customers only.</li>
      <li>All services include fly screen, sill and tracks cleaned as well as cobweb removal.</li>
      <li>Houses with more than 20 windows (or two levels) will have an immediate quote provided upon inspection of the property with 20% discount applied.</li>
      <li>Kelda’s Window Washing Services are fully insured.</li>
    </ul>
  </main>
</body>
</html>
```